Technical Communications firm needs an article turned into a white paper

We want to redesign a 3-part blog series into a white paper that we can print for a conference. I've consolidated the three posts into the attached Word document.

We are looking for a light, easy to read design. Good use of graphics to support the message. I've added the graphics we used in the original post.

You can view them at
http://www.brightquillpages.com/blog/are-you-satisfied-with-your-dita-solution/

Target Market(s)

Product managers from High-tech, Finance, and Medical industries.

Industry/Entity Type

Information Technology

Colors

Designer to choose colors to be used in the design.

Requirements
Must have
• Must be modern, light, easy to read and slick design. Try to incorporate the graphics provided, but feel free to add more. Must retain the lists and tables.
• Must align with our website/brand.
• Must be easy to read. So not too busy.
• Please move all footnotes to endnotes. You'll need to rework the numbering.
Nice to have
• Awesome coverpage.
Should not have
• Hokey clipart. Not too heavy or hard to read.

```html
<!DOCTYPE html>
<html lang="en">
<head>
<meta charset="utf-8">
<title>Are You Satisfied With Your DITA Solution? – White Paper Spread</title>
<link href="https://fonts.googleapis.com/css2?family=Montserrat:wght@400;600;700&family=Source+Sans+3:ital,wght@0,400;0,600;1,400&display=swap" rel="stylesheet">
<style>
  :root {
    --bg: #e4e3df;
    --paper: #ffffff;
    --navy: #27458f;
    --navy-deep: #1f3a7d;
    --sky: #4aa3d8;
    --sky-light: #5aaee0;
    --ink: #3c3f44;
    --muted: #6b6f75;
    --teal: #6bb38f;
    --lime: #a9c65a;
    --gold: #d9b23a;
    --board: #50585f;
  }
  * { box-sizing: border-box; margin: 0; padding: 0; }
  html, body { width: 1200px; height: 804px; overflow: hidden; background: var(--bg); }
  body { font-family: "Source Sans 3", sans-serif; color: var(--ink); position: relative; }

  .spread {
    position: absolute; left: 40px; top: 24px; width: 1120px; height: 756px;
    display: flex; box-shadow: 0 10px 30px rgba(0,0,0,.18);
  }
  .page { position: relative; width: 560px; height: 756px; background: var(--paper); overflow: hidden; }
  .page--left { background: linear-gradient(90deg, #fff 85%, #eeeeee 100%); }
  .page--right { background: linear-gradient(90deg, #ebebeb 0%, #fff 12%); }

  /* Left page */
  .hero-photo {
    position: absolute; left: 0; top: 0; width: 560px; height: 330px;
    background: radial-gradient(circle at 78% 70%, #8a5a3f 0 60px, transparent 62px),
                linear-gradient(160deg, #5b636a 0%, var(--board) 60%, #464d53 100%);
  }
  .article { position: absolute; left: 46px; top: 362px; right: 40px; }
  .article__title {
    font-family: "Montserrat", sans-serif; font-weight: 700; font-size: 27px;
    line-height: 1.45; letter-spacing: -0.5px; color: var(--navy); text-transform: uppercase;
  }
  .article__title .accent { color: var(--sky); }
  .byline { margin-top: 22px; font-size: 14px; font-style: italic; color: var(--ink); }
  .byline__role { display: block; margin-top: 8px; font-size: 10.5px; }
  .article__body p { font-size: 10.5px; line-height: 1.55; margin-top: 18px; text-align: justify; }
  .article__body p + p { margin-top: 10px; }

  .footer { position: absolute; left: 0; bottom: 0; width: 560px; height: 74px; }
  .footer svg { position: absolute; inset: 0; }
  .footer__contact {
    position: absolute; left: 28px; bottom: 12px; color: #fff; font-size: 11px; letter-spacing: .2px;
  }
  .footer__page {
    position: absolute; bottom: 40px; color: #fff; font-family: "Montserrat", sans-serif;
    font-size: 10px; letter-spacing: .5px;
  }
  .page--left .footer__page { right: 56px; }
  .page--right .footer__page { left: 70px; }
  .page--right .footer__contact { left: auto; right: 40px; bottom: 30px; }

  /* Right page */
  .site-tab { position: absolute; right: 0; top: 0; width: 200px; height: 52px; }
  .site-tab svg { position: absolute; inset: 0; }
  .site-tab__url { position: absolute; right: 22px; top: 14px; color: #fff; font-size: 10px; }
  .content { position: absolute; left: 50px; right: 40px; top: 108px; }
  .section-title {
    font-family: "Montserrat", sans-serif; font-weight: 600; font-size: 19px; color: var(--sky);
  }
  .intro { font-size: 10.5px; line-height: 1.5; margin-top: 8px; }
  .categories { display: flex; justify-content: center; gap: 34px; margin: 20px 0 18px; }
  .category { text-align: center; width: 96px; }
  .category__num {
    height: 40px; display: flex; align-items: center; justify-content: center;
    color: #fff; font-family: "Montserrat", sans-serif; font-weight: 700; font-size: 15px;
  }
  .category--skills .category__num { background: var(--teal); }
  .category--tech .category__num { background: var(--lime); }
  .category--mgmt .category__num { background: var(--gold); }
  .category__label { display: block; margin-top: 8px; font-size: 10px; color: var(--muted); }
  .note { font-size: 10.5px; line-height: 1.5; }
  .section-title--issues { margin-top: 22px; }
  .issues { list-style: none; margin-top: 20px; }
  .issue { display: flex; gap: 16px; margin-bottom: 24px; }
  .issue__icon { flex: 0 0 44px; height: 44px; }
  .issue__head { font-family: "Montserrat", sans-serif; font-weight: 600; font-size: 12.5px; color: var(--ink); }
  .issue__head span { color: var(--sky); }
  .issue__text { font-size: 10.5px; line-height: 1.5; margin-top: 4px; }
</style>
</head>
<body>
<main class="spread">
  <section class="page page--left">
    <div class="hero-photo" role="img" aria-label="Photo of a bearded man looking sideways in front of a chalkboard with rows of hand-drawn yellow rating stars and checkboxes"></div>

    <article class="article">
      <h1 class="article__title"><span class="accent">Are you satisfied</span> with your<br>DITA solution?</h1>
      <p class="byline">By Dana Whitfield
        <span class="byline__role">President of Brightquill Authoring Solutions Inc.</span></p>
      <div class="article__body">
        <p>If your answer is “No” then you are not alone according to a 2017 survey of more than 250 technical communication professionals conducted by The Copy Ranger. The DITA Satisfaction Survey[i] indicates that 62% of respondents using DITA are—to varying degrees—dissatisfied. As many as 10% of that group were very dissatisfied reporting that their DITA implementation is experiencing ‘big’ challenges. It’s not surprising that there’s significant dissatisfaction amongst those who have adopted DITA. After all, moving to DITA is a seismic shift in technical writing; a big change with many opportunities for things to go wrong.</p>
        <p>The good news is that most DITA users don’t see their problems as insurmountable. Many just need a little help getting to where they’d like to be.</p>
      </div>
    </article>

    <footer class="footer">
      <svg width="560" height="74" viewBox="0 0 560 74" aria-hidden="true">
        <polygon points="370,22 560,22 560,74 0,74 0,60 350,42" fill="var(--navy)"/>
        <polygon points="0,50 356,50 370,36 370,42 360,58 0,62" fill="var(--sky-light)"/>
        <polygon points="0,48 350,48 366,34 372,34 356,74 0,74" fill="var(--sky-light)"/>
        <polygon points="0,66 560,66 560,74 0,74" fill="var(--navy-deep)"/>
      </svg>
      <p class="footer__contact">Phone: +1 (555) 014-2780 &nbsp;|&nbsp; more-info@brightquillpages.com</p>
      <p class="footer__page">PAGE 2 OF 10</p>
    </footer>
  </section>

  <section class="page page--right">
    <div class="site-tab">
      <svg width="200" height="52" viewBox="0 0 200 52" aria-hidden="true">
        <polygon points="0,10 200,10 200,40 30,40 18,52 0,52" fill="var(--navy)"/>
        <polygon points="0,0 200,0 200,10 0,10" fill="var(--navy-deep)"/>
      </svg>
      <span class="site-tab__url">www.brightquillpages.com</span>
    </div>

    <div class="content">
      <h2 class="section-title">Breakdown of the issues</h2>
      <p class="intro">The Copy Ranger DITA Satisfaction Survey asked respondents to rank the top 10 issues facing DITA users. These issues fit into three major categories including</p>

      <div class="categories">
        <div class="category category--skills"><div class="category__num">01</div><span class="category__label">Skills Development</span></div>
        <div class="category category--tech"><div class="category__num">02</div><span class="category__label">Technology</span></div>
        <div class="category category--mgmt"><div class="category__num">03</div><span class="category__label">Management</span></div>
      </div>

      <p class="note">The DITA Satisfaction Survey Aggregate Results revealed little spread between the ranking of the issues indicating that respondents likely faced more than one issue of concern.</p>

      <h2 class="section-title section-title--issues">Issues discussed in this article</h2>
      <p class="intro">In this article, we examine three issues impacting DITA satisfaction to help you find the best place to start making improvements.</p>

      <ol class="issues">
        <li class="issue">
          <svg class="issue__icon" viewBox="0 0 44 44" aria-hidden="true" fill="none" stroke="var(--sky)" stroke-width="1.6">
            <path d="M10 38 V30 C5 26 5 16 10 11 C16 5 28 5 33 12 C36 17 36 21 38 25 L34 26 V31 H29 V38"/>
            <circle cx="21" cy="19" r="7"/><circle cx="21" cy="19" r="3"/>
          </svg>
          <div>
            <h3 class="issue__head">1. Part-1: <span>Skills Development</span></h3>
            <p class="issue__text">This problem area is far and away the most pressing obstacle for a successful DITA deployment. Too often authors are left to figure out how to adapt to writing for DITA on their own.</p>
          </div>
        </li>
        <li class="issue">
          <svg class="issue__icon" viewBox="0 0 44 44" aria-hidden="true" fill="none" stroke="var(--sky)" stroke-width="1.6">
            <rect x="8" y="20" width="28" height="16" rx="2"/><path d="M22 36 V41 M16 41 H28"/>
            <path d="M14 20 V8 M22 20 V4 M30 20 V10"/><circle cx="14" cy="7" r="2"/><circle cx="30" cy="9" r="2"/>
          </svg>
          <div>
            <h3 class="issue__head">2. Part-2: <span>Technology</span></h3>
            <p class="issue__text">We often hear about the failure of the technology as it relates to performance or complexity. While technology may seem the most likely culprit, it is often not the root cause of the problem.</p>
          </div>
        </li>
        <li class="issue">
          <svg class="issue__icon" viewBox="0 0 44 44" aria-hidden="true">
            <circle cx="16" cy="12" r="6" fill="var(--sky)"/>
            <path d="M5 38 C5 26 10 21 16 21 C22 21 26 25 27 30 V38 Z" fill="var(--sky)"/>
            <circle cx="33" cy="30" r="6" fill="none" stroke="var(--sky)" stroke-width="2.5" stroke-dasharray="3 2"/>
            <circle cx="33" cy="30" r="2" fill="var(--sky)"/>
          </svg>
          <div>
            <h3 class="issue__head">3. Part-3: <span>Management</span></h3>
            <p class="issue__text">While these issues appear to be of least concern to many survey respondents, they are most likely to form the root cause of all other issues identified in the survey. This points to a general lack of awareness as to the role management should be playing in collaborative, structured authoring solutions.</p>
          </div>
        </li>
      </ol>
    </div>

    <footer class="footer">
      <svg width="560" height="74" viewBox="0 0 560 74" aria-hidden="true">
        <polygon points="0,26 190,26 206,42 560,42 560,74 0,74" fill="var(--navy)"/>
        <polygon points="196,40 560,40 560,58 214,58" fill="var(--sky-light)"/>
        <polygon points="190,20 560,20 560,26 196,26" fill="var(--sky-light)" opacity="0"/>
      </svg>
      <p class="footer__page">PAGE 3 OF 10</p>
      <p class="footer__contact" style="bottom:19px">Phone: +1 (555) 014-2780 &nbsp;|&nbsp; more-info@brightquillpages.com</p>
    </footer>
  </section>
</main>
</body>
</html>
```